Lumvra App | Pre-Launch Homepage

Dear designer,
Lumvra is a soon to be launched innovative & free social platform for collaborative addictions quitting.
We require a design for our pre-launch homepage that will elevate our basic wireframes to the next level.
We would like the wireframes to serve as a guideline only, and not as a final version of the design. If you have cool ideas - we would appreciate your creativity!
* This is a pre-launch website for a mobile app, and as such the design must be consistent with the general style, design and atmosphere of the app (see screenshot in the shared Drive link).
* We liked the style and feel of the following website: http://tandelhub.example/ - Please let's use it as a reference as well.
* The existing text in the wireframes is there just to represent a place for text. Copy will be edited by us after the design is done.
Please find the wireframes attached, and all relevant design assets and app screenshots in the following Drive shared link -
https://files.example-share.net/open?id=7KQ204RtP3mNxa8Y2Lb61H9cdVzQ
Thanks,
Reginald
Industry/Entity Type
Social
Number of Pages Required
1 page
Look and feel
Each slider illustrates characteristics of the customer's brand and the style your logo design should communicate.

```html
<!DOCTYPE html>
<html lang="en">
<head>
<meta charset="utf-8">
<title>Lumvra App | Pre-Launch Homepage</title>
<link rel="stylesheet" href="https://fonts.googleapis.com/css2?family=Open+Sans:wght@400;600;700&display=swap">
<style>
:root{
  --orange:#f7941d;
  --orange-dark:#e9820c;
  --green:#7cb41c;
  --ink:#333333;
  --muted:#666666;
  --night:#23232a;
  --grey:#e6e6e6;
  --white:#ffffff;
}
*{box-sizing:border-box;margin:0;padding:0}
html,body{width:1200px;height:3276px;overflow:hidden}
body{font-family:"Open Sans",Arial,sans-serif;color:var(--ink);background:var(--white);position:relative}
section,header,footer{position:absolute;left:0;width:1200px;overflow:hidden}

.topbar{top:0;height:36px;background:#2a2a2a;color:#ddd;font-size:14px}
.topbar .contact{position:absolute;right:40px;top:8px;display:flex;align-items:center;gap:8px}
.topbar .contact i{width:20px;height:20px;border-radius:50%;background:#ddd;display:block}

.brand{top:36px;height:152px;background:var(--white);text-align:center}
.brand .name{margin-top:30px;font-size:60px;font-weight:700;color:var(--orange);line-height:1}
.brand .tagline{margin-top:14px;font-size:15px;font-weight:600;color:#444}

.hero{top:188px;height:540px;color:var(--white);text-align:center;
  background:radial-gradient(ellipse at 50% 30%,#6b4a34 0%,#3c2d27 45%,#1d1a1f 100%)}
.hero h1{margin:70px auto 0;width:820px;font-size:40px;font-weight:600;line-height:1.3}
.subscribe{width:600px;margin:0 auto;border:2px solid rgba(255,255,255,.35);background:rgba(0,0,0,.25);padding:22px 30px 30px}
.subscribe p{font-size:15px;font-weight:600;letter-spacing:1px;margin-bottom:18px}
.subscribe .row{display:flex;justify-content:center}
.subscribe .field{width:300px;height:38px;background:var(--white);color:#999;font-size:13px;text-align:left;padding:10px 14px}
.subscribe .btn{width:140px;height:38px;background:var(--green);color:var(--white);font-size:13px;font-weight:700;padding-top:10px}
.hero .subscribe{margin-top:64px}
.devices{margin-top:48px;display:flex;justify-content:center;align-items:flex-end;gap:40px}
.pager{position:absolute;left:540px;top:508px;display:flex;gap:14px;z-index:2}
.pager span{width:48px;height:48px;border-radius:50%;background:rgba(255,255,255,.85);display:flex;align-items:center;justify-content:center}

.values{top:728px;height:392px;background:var(--orange);color:var(--white);display:flex;justify-content:center;gap:110px;padding-top:90px}
.value{width:230px;text-align:center}
.value .badge{width:128px;height:128px;border-radius:50%;background:var(--white);margin:0 auto;display:flex;align-items:center;justify-content:center}
.value h3{margin-top:30px;font-size:17px;letter-spacing:2px;font-weight:700}
.value p{margin-top:12px;font-size:15px;line-height:1.4}

.split h2{font-size:40px;font-weight:600;color:var(--orange);letter-spacing:2px}
.split p{font-size:16px;line-height:1.6;margin-top:14px}
.fun{top:1120px;height:340px;background:linear-gradient(90deg,#1c1e26,#2c2e38);color:#ccc}
.fun .art{position:absolute;left:120px;top:50px;width:240px;height:240px;border-radius:50%;background:radial-gradient(circle,#3a3c46,#24262e)}
.fun .copy{position:absolute;left:410px;top:50px;width:620px}
.inspire{top:1460px;height:340px;background:var(--grey)}
.inspire .copy{position:absolute;left:170px;top:66px;width:600px;text-align:center}
.inspire .copy h2{text-align:right;padding-right:40px}
.inspire .art{position:absolute;left:800px;top:60px;width:180px;height:220px;border-radius:40%;background:radial-gradient(circle,#c9c9c9,#e6e6e6 70%)}

.achieve{top:1800px;height:540px;background:var(--white);text-align:center}
.achieve h2{margin-top:50px;font-size:40px;font-weight:600;color:var(--orange);letter-spacing:2px}
.achieve .lead{width:560px;margin:12px auto 0;font-size:16px;line-height:1.5;color:var(--muted)}
.achieve .trophy{position:absolute;left:470px;top:220px;width:260px;height:290px;background:radial-gradient(ellipse at 50% 40%,#e8c34a,#b88a1a 55%,#fff 72%)}
.feature{position:absolute;width:330px;display:flex;gap:16px;align-items:flex-start;font-size:14px;line-height:1.45;color:var(--muted);text-align:left}
.feature .ring{flex:none;width:56px;height:56px;border-radius:50%;border:2px solid var(--orange);display:flex;align-items:center;justify-content:center}
.feature.right{flex-direction:row-reverse;text-align:right}

.coming{top:2340px;height:720px;color:var(--white);text-align:center;
  background:radial-gradient(ellipse at 60% 40%,#5c4a4e 0%,#3a3236 50%,#1f1c21 100%)}
.coming h2{margin-top:80px;font-size:40px;font-weight:600;letter-spacing:2px}
.coming .phones{position:absolute;left:430px;top:160px;width:340px;height:260px;border-radius:40% 40% 10% 10%;background:radial-gradient(circle at 50% 55%,#e06a2a,#7a4ab0 45%,rgba(60,60,80,0) 75%)}
.coming .nav{position:absolute;top:260px;font-size:40px;color:rgba(255,255,255,.6)}
.stores{position:absolute;top:455px;left:0;width:1200px;display:flex;justify-content:center;gap:44px}
.stores span{width:62px;height:62px;background:var(--white);border-radius:12px}
.coming .subscribe{position:absolute;left:300px;top:565px}

.site-footer{top:3060px;height:216px;background:var(--orange);color:var(--white);text-align:center}
.site-footer h4{margin-top:54px;font-size:20px;letter-spacing:3px;font-weight:600}
.social{margin-top:22px;display:flex;justify-content:center;gap:8px}
.social span{width:30px;height:30px;border-radius:50%;background:var(--white)}
.legal{margin-top:20px;font-size:12px;letter-spacing:1px}
.totop{position:absolute;right:30px;top:150px;width:36px;height:36px;background:#333}
</style>
</head>
<body>

<header class="topbar"><div class="contact">Contact Us <i></i></div></header>

<header class="brand">
  <div class="name">Lumvra</div>
  <div class="tagline">Become a Better Version of Yourself</div>
</header>

<section class="hero" role="img" aria-label="Blurred warm-toned background photo of people together">
  <h1>Lumvra is a revolutionary &amp; free social platform for collaborative addictions quitting.</h1>
  <div class="subscribe">
    <p>SUBSCRIBE BELOW FOR THE RELEASE &amp; UPDATES</p>
    <div class="row"><div class="field">Enter your e-mail address</div><div class="btn">LET ME KNOW!</div></div>
  </div>
  <div class="devices">
    <svg width="22" height="40" viewBox="0 0 22 40"><rect x="2" y="2" width="18" height="36" rx="3" fill="none" stroke="#fff" stroke-width="3"/><circle cx="11" cy="33" r="2" fill="#fff"/></svg>
    <svg width="34" height="44" viewBox="0 0 34 44"><rect x="2" y="2" width="30" height="40" rx="3" fill="none" stroke="#fff" stroke-width="3"/><circle cx="17" cy="37" r="2" fill="#fff"/></svg>
    <svg width="56" height="48" viewBox="0 0 56 48"><rect x="2" y="2" width="52" height="34" rx="2" fill="none" stroke="#fff" stroke-width="3"/><path d="M22 38v6h12v-6M16 46h24" stroke="#fff" stroke-width="3" fill="none"/></svg>
  </div>
  <div class="pager">
    <span><svg width="16" height="16" viewBox="0 0 16 16"><path d="M10 3L5 8l5 5" stroke="#888" stroke-width="2" fill="none"/></svg></span>
    <span><svg width="16" height="16" viewBox="0 0 16 16"><path d="M6 3l5 5-5 5" stroke="#888" stroke-width="2" fill="none"/></svg></span>
  </div>
</section>

<section class="values">
  <div class="value">
    <div class="badge"><svg width="70" height="70" viewBox="0 0 70 70"><circle cx="35" cy="35" r="28" fill="none" stroke="#e0463a" stroke-width="12" stroke-dasharray="22 22"/><circle cx="35" cy="35" r="28" fill="none" stroke="#ddd" stroke-width="12" stroke-dasharray="22 22" stroke-dashoffset="22"/></svg></div>
    <h3>NEVER BE ALONE</h3><p>Forget what you know - Lumvra makes it fun to quit.</p>
  </div>
  <div class="value">
    <div class="badge"><svg width="70" height="70" viewBox="0 0 70 70"><path d="M35 4l9 21 23 2-17 15 5 23-20-12-20 12 5-23L3 27l23-2z" fill="#e8b62a"/></svg></div>
    <h3>NETWORK POWER</h3><p>Forget what you know - Lumvra makes it fun to quit.</p>
  </div>
  <div class="value">
    <div class="badge"><svg width="70" height="70" viewBox="0 0 70 70"><circle cx="35" cy="35" r="24" fill="none" stroke="#777" stroke-width="10" stroke-dasharray="8 6"/><circle cx="35" cy="35" r="12" fill="#999"/></svg></div>
    <h3>STAY MOTIVATED</h3><p>Forget what you know - Lumvra makes it fun to quit.</p>
  </div>
</section>

<section class="fun split">
  <div class="art" role="img" aria-label="Large white line illustration of a cheerful emoticon"></div>
  <div class="copy">
    <h2>FUN</h2>
    <p>Forget what you know - Lumvra makes it fun to quit. The battle between your good and bad demons comes to life in our gamified approach for managing your campaigns.</p>
    <p>Lumvra gives you the opportunity to take an active role in helping your network to smash your common addictions as a team. That's right, we converted the obsession process into a social game.</p>
  </div>
</section>

<section class="inspire split">
  <div class="copy">
    <h2>INSPIRE</h2>
    <p>One of the most important factors for successful quitting is the ability to stay inspired during the process.</p>
    <p>That's why we designed Lumvra as a platform where you can inspire and be inspired by a supportive network of awesome Lumvra ninjas!</p>
  </div>
  <div class="art" role="img" aria-label="Line illustration of a glowing light bulb"></div>
</section>

<section class="achieve">
  <h2>ACHIEVE</h2>
  <p class="lead">Lumvra is built as a pyramid of relationships that makes use of the Social Cognitive Theory, to provide a powerful network of positive reinforcement. The bigger you make it the stronger you get.</p>
  <div class="trophy" role="img" aria-label="Illustration of a golden trophy cup"></div>
  <div class="feature" style="left:100px;top:270px"><span class="ring"><svg width="24" height="24" viewBox="0 0 24 24"><path d="M12 2l8 3v6c0 6-4 9-8 11-4-2-8-5-8-11V5z" fill="var(--orange)"/></svg></span><span>Lorem ipsum dolor sit amet, consectetur adipiscing elit, sed do eiusmod tempor incididunt ut labore et dolore</span></div>
  <div class="feature" style="left:100px;top:370px"><span class="ring"><svg width="24" height="24" viewBox="0 0 24 24"><path d="M2 11L22 2l-6 20-4-8z" fill="var(--orange)"/></svg></span><span>Lorem ipsum dolor sit amet, consectetur adipiscing elit, sed do eiusmod tempor incididunt ut labore et dolore</span></div>
  <div class="feature right" style="left:770px;top:270px"><span class="ring"><svg width="24" height="24" viewBox="0 0 24 24"><circle cx="10" cy="10" r="6" fill="none" stroke="var(--orange)" stroke-width="3"/><path d="M15 15l6 6" stroke="var(--orange)" stroke-width="3"/></svg></span><span>Lorem ipsum dolor sit amet, consectetur adipiscing elit, sed do eiusmod tempor incididunt ut labore et dolore</span></div>
  <div class="feature right" style="left:770px;top:370px"><span class="ring"><svg width="24" height="24" viewBox="0 0 24 24"><path d="M18 5L6 12l12 7" stroke="var(--orange)" stroke-width="2" fill="none"/><circle cx="18" cy="5" r="3" fill="var(--orange)"/><circle cx="6" cy="12" r="3" fill="var(--orange)"/><circle cx="18" cy="19" r="3" fill="var(--orange)"/></svg></span><span>Lorem ipsum dolor sit amet, consectetur adipiscing elit, sed do eiusmod tempor incididunt ut labore et dolore</span></div>
</section>

<section class="coming" role="img" aria-label="Blurred dark background photo">
  <h2>COMMING SOON</h2>
  <span class="nav" style="left:250px">&lsaquo;</span>
  <span class="nav" style="right:250px">&rsaquo;</span>
  <div class="phones" role="img" aria-label="Illustration of a smartphone surrounded by colourful app icons"></div>
  <div class="stores"><span></span><span></span><span></span></div>
  <div class="subscribe">
    <p>SUBSCRIBE BELOW FOR THE RELEASE &amp; UPDATES</p>
    <div class="row"><div class="field">Enter your e-mail address</div><div class="btn">LET ME KNOW!</div></div>
  </div>
</section>

<footer class="site-footer">
  <h4>JOIN THE REVOLUTION</h4>
  <div class="social"><span></span><span></span><span></span><span></span><span></span></div>
  <p class="legal">COPYRIGHT © 2015 LUMVRA.EXAMPLE &nbsp;·&nbsp; CONTACT US &nbsp;·&nbsp; T&amp;CS &nbsp;·&nbsp; PRIVACY POLICY</p>
  <div class="totop"></div>
</footer>

</body>
</html>
```